Modern Business Card

Modern professional business card with more than just logo and demographic info. Something memorable.

We are a trendy/modern chiropractic group with an emphasis on neurology, hence the minimalist-type brain logo. We want to convey that modern and technical aspect with professionalism and the elite nature of our practice environment.

```html
<!DOCTYPE html>
<html lang="en">
<head>
<meta charset="utf-8">
<title>Axiom Chiropractic — Business Card</title>
<link rel="stylesheet" href="https://fonts.googleapis.com/css2?family=Bitter:wght@700&family=Crimson+Pro:wght@400&family=Arimo:wght@400&display=swap">
<style>
  :root {
    --backdrop: #d9d9d9;
    --card-white: #ffffff;
    --brand-blue: #3f7bc4;
    --back-blue: #4a80c6;
    --ink: #1f1f1f;
    --ink-soft: #333333;
    --band-grey: #5a5a5a;
    --rule: #dcdcdc;
    --wash: #efefef;
  }
  * { box-sizing: border-box; margin: 0; padding: 0; }
  html, body { width: 1200px; height: 802px; overflow: hidden; }
  body { background: var(--backdrop); position: relative; font-family: "Arimo", Arial, sans-serif; }

  .card {
    position: absolute;
    top: 274px;
    width: 442px;
    height: 265px;
    box-shadow: 0 3px 6px rgba(0,0,0,0.35);
    overflow: hidden;
  }
  .card--front { left: 136px; background: var(--card-white); }
  .card--back { left: 625px; background: var(--back-blue); }

  /* front */
  .front-wash {
    position: absolute; left: 0; top: 0; width: 270px; height: 240px;
    background: linear-gradient(90deg, var(--wash) 0%, rgba(239,239,239,0.7) 65%, rgba(255,255,255,0) 100%);
    -webkit-mask-image: linear-gradient(180deg, #000 0%, #000 55%, transparent 100%);
    mask-image: linear-gradient(180deg, #000 0%, #000 55%, transparent 100%);
  }
  .brand-mark {
    position: absolute; left: 176px; top: 56px; width: 44px; height: 44px;
    background: var(--brand-blue);
  }
  .brand-name {
    position: absolute; left: 231px; top: 50px;
    font-family: "Crimson Pro", Georgia, serif; font-weight: 400;
    color: var(--ink); line-height: 1;
  }
  .brand-name__primary { display: block; font-size: 48px; letter-spacing: 0.5px; }
  .brand-name__secondary { display: block; font-size: 27.5px; letter-spacing: 0.4px; margin-top: -4px; }

  .holder { position: absolute; left: 27px; top: 153px; width: 411px; }
  .holder__row { display: flex; align-items: center; gap: 6px; }
  .holder__name {
    font-family: "Bitter", Georgia, serif; font-weight: 700;
    font-size: 14px; color: var(--brand-blue); letter-spacing: 0.3px; white-space: nowrap;
  }
  .holder__rule { flex: 1; height: 1px; background: var(--rule); }
  .holder__title { font-size: 12.5px; color: var(--ink-soft); margin-top: 1px; }

  .contact { position: absolute; left: 27px; top: 196px; list-style: none; }
  .contact li { display: flex; align-items: center; gap: 5px; font-size: 12.8px; color: var(--ink-soft); height: 16px; white-space: nowrap; }
  .contact svg { width: 13px; height: 13px; flex: none; }
  .contact .accent { color: var(--brand-blue); }

  .address {
    position: absolute; right: 30px; top: 212px; text-align: right;
    font-size: 12.8px; color: var(--ink-soft); line-height: 16px; font-style: normal; white-space: nowrap;
  }
  .footer-bands { position: absolute; left: 0; bottom: 0; width: 442px; height: 12px; }

  /* back */
  .back-pattern { position: absolute; inset: 0; background: var(--back-blue); }
  .back-name {
    position: absolute; left: 0; right: 0; top: 132px; text-align: center;
    font-family: "Crimson Pro", Georgia, serif; font-weight: 400;
    color: var(--card-white); line-height: 1; transform: translateY(-50%);
  }
  .back-name__primary { display: block; font-size: 62px; letter-spacing: 0.5px; }
  .back-name__secondary { display: block; font-size: 34.5px; letter-spacing: 0.5px; margin-top: -6px; }
</style>
</head>
<body>

  <section class="card card--front" aria-label="Business card front">
    <div class="front-wash" role="img" aria-label="Faint oversized brand symbol decoration"></div>

    <div class="brand-mark" aria-hidden="true"></div>
    <div class="brand-name">
      <span class="brand-name__primary">AXIOM</span>
      <span class="brand-name__secondary">CHIROPRACTIC</span>
    </div>

    <div class="holder">
      <div class="holder__row">
        <span class="holder__name">DANIEL HARPER</span>
        <span class="holder__rule"></span>
      </div>
      <div class="holder__title">Managing Director</div>
    </div>

    <ul class="contact">
      <li>
        <svg viewBox="0 0 14 14" aria-hidden="true"><rect x="0.75" y="0.75" width="12.5" height="12.5" rx="2" fill="none" stroke="var(--brand-blue)" stroke-width="1.3"/><path d="M4.2 3.3l1.4 1.6-.8 1a5 5 0 0 0 2.4 2.4l1-.8 1.6 1.4-.7 1.4c-3 0-5.8-2.8-5.8-5.8z" fill="var(--brand-blue)"/></svg>
        044-987 654 321
      </li>
      <li>
        <svg viewBox="0 0 14 14" aria-hidden="true"><rect x="0.5" y="2.5" width="13" height="9" fill="var(--brand-blue)"/><path d="M0.8 2.8L7 7.6l6.2-4.8M0.8 11.2l4.6-4.2M13.2 11.2L8.6 7" fill="none" stroke="#fff" stroke-width="1"/></svg>
        hello@axiomchiro.com
      </li>
      <li>
        <svg viewBox="0 0 14 14" aria-hidden="true"><g fill="none" stroke="var(--brand-blue)" stroke-width="1.2"><circle cx="7" cy="7" r="6"/><ellipse cx="7" cy="7" rx="2.6" ry="6"/><path d="M1 7h12M2 4h10M2 10h10"/></g></svg>
        <span>www.<span class="accent">axiomchiro</span>.com</span>
      </li>
    </ul>

    <address class="address">
      18, Linden Street North<br>
      Fairmont City, 60718
    </address>

    <svg class="footer-bands" viewBox="0 0 442 12" aria-hidden="true">
      <rect x="0" y="4" width="226" height="8" fill="var(--brand-blue)"/>
      <polygon points="234,0 442,0 442,12 229,12" fill="var(--band-grey)"/>
    </svg>
  </section>

  <section class="card card--back" aria-label="Business card back">
    <div class="back-pattern" role="img" aria-label="Repeating pattern of the brand symbol in lighter blue"></div>
    <div class="back-name">
      <span class="back-name__primary">AXIOM</span>
      <span class="back-name__secondary">CHIROPRACTIC</span>
    </div>
  </section>

</body>
</html>
```